Timber Crest Construction Needs business card

Hey we are in need of business card designs. I have upload our logo as a guideline, but free feel to run with it or come up with something unique.
Pls have fun with it and be creative. the name says it all!
i will give some directions after i see a few entries..
Updates
Logo source file has been uploaded..
Hey because of the logo is so colourful already.
Can we have a few submissions with less colour.
Also we are looking for clever/hidden/descriptive business card.

```html
<!DOCTYPE html>
<html lang="en">
<head>
<meta charset="utf-8">
<title>Timber Crest Construction – Business Card</title>
<link rel="stylesheet" href="https://fonts.googleapis.com/css2?family=Questrial&display=swap">
<style>
  :root {
    --backdrop: #1f8a06;
    --card-dark: #000000;
    --card-light: #ffffff;
    --brand-grey: #7b7b7d;
    --ink: #2a2a2a;
    --accent-red: #e3262f;
  }
  * { margin: 0; padding: 0; box-sizing: border-box; }
  html, body {
    width: 1200px; height: 1200px; overflow: hidden;
    background: var(--backdrop);
    font-family: "Questrial", "Century Gothic", sans-serif;
  }
  .canvas { position: relative; width: 1200px; height: 1200px; }
  .card {
    position: absolute; left: 212px; width: 800px; height: 445px;
  }
  .card--front { top: 130px; background: var(--card-dark); }
  .card--back { top: 641px; background: var(--card-light); }

  .wordmark {
    position: absolute; text-align: center;
    color: var(--brand-grey); text-transform: uppercase; line-height: 1;
  }
  .wordmark__name { display: block; font-size: 40px; letter-spacing: 1px; }
  .wordmark__sub { display: block; font-size: 15px; letter-spacing: 2px; margin-top: 8px; }
  .card--front .wordmark { left: 0; right: 0; top: 245px; }
  .card--back .wordmark { left: 60px; width: 330px; top: 238px; }
  .card--back .wordmark__name { font-size: 36px; }

  .contact { position: absolute; left: 443px; top: 123px; color: var(--ink); }
  .contact__name { font-size: 15px; letter-spacing: 4px; font-weight: 700; }
  .contact__name .sep { color: #777; margin: 0 8px; letter-spacing: 0; }
  .contact__role { color: var(--accent-red); font-weight: 400; letter-spacing: 2.5px; font-size: 14px; }
  .contact__address { margin-top: 30px; font-size: 14px; letter-spacing: 2.6px; line-height: 21px; }
  .contact__list { list-style: none; margin-top: 23px; }
  .contact__item {
    display: flex; align-items: center; height: 25px;
    font-size: 14px; letter-spacing: 2.6px;
  }
  .contact__item svg { width: 16px; height: 16px; margin-right: 20px; flex: none; }
</style>
</head>
<body>
<div class="canvas">
  <section class="card card--front">
    <div class="wordmark">
      <span class="wordmark__name">Timber Crest</span>
      <span class="wordmark__sub">Construction</span>
    </div>
  </section>

  <section class="card card--back">
    <div class="wordmark">
      <span class="wordmark__name">Timber Crest</span>
      <span class="wordmark__sub">Construction</span>
    </div>

    <div class="contact">
      <p class="contact__name">MARTA QUINN<span class="sep">-</span><span class="contact__role">DIRECTOR</span></p>
      <p class="contact__address">SHOP 4, 212-216 HARBOUR<br>ROAD WESTMERE NORTH</p>
      <ul class="contact__list">
        <li class="contact__item">
          <svg viewBox="0 0 16 16" aria-hidden="true"><path d="M1 6c0-3 3-4 7-4s7 1 7 4l-3 1-1-2H5L4 7z" fill="var(--accent-red)"/><path d="M4 9h8l1 5H3z" fill="none" stroke="var(--accent-red)" stroke-width="1.5"/><circle cx="8" cy="11.5" r="1.3" fill="var(--accent-red)"/></svg>
          5071 2093
        </li>
        <li class="contact__item">
          <svg viewBox="0 0 16 16" aria-hidden="true" fill="none" stroke="var(--accent-red)" stroke-width="1.5"><rect x="4" y="1.5" width="8" height="4"/><rect x="1.5" y="5.5" width="13" height="6" rx="1"/><rect x="4" y="9.5" width="8" height="5"/></svg>
          5071 2094
        </li>
        <li class="contact__item">
          <svg viewBox="0 0 16 16" aria-hidden="true" fill="none" stroke="var(--accent-red)" stroke-width="1.5"><rect x="1.5" y="3.5" width="13" height="9"/><path d="M1.5 3.5 8 9l6.5-5.5"/></svg>
          marta@timbercrestbuild.com
        </li>
        <li class="contact__item">
          <svg viewBox="0 0 16 16" aria-hidden="true" fill="none" stroke="var(--accent-red)" stroke-width="1.3"><circle cx="7.5" cy="7.5" r="6"/><ellipse cx="7.5" cy="7.5" rx="2.6" ry="6"/><path d="M1.5 7.5h12M2.5 4.5h10M2.5 10.5h10"/><path d="M10 10l5 2-2 1-1 2z" fill="var(--accent-red)" stroke="none"/></svg>
          www.timbercrestbuild.com
        </li>
      </ul>
    </div>
  </section>
</div>
</body>
</html>
```